velorimo.gr wordpress makeover

We need a makeover of our wordpress website velorimo.gr We are a company that provides astrology services via phone either by billable phone number or by prepaid packages.This is what we sell. Moreover, we share everyday astrology related articles to our blog. It will be a multy page website. Our goal is always to sell our phone prepaid packages or to make the visitor of the website call our billable numbers. Our website should have:
-a home page introducing its content (astrologers, call packages, blog section with categories).
-astrologers page (you can see the existing one to understand)
-Phone packages page (eshop page where you can buy prepaid phone packages. woo commerce maybe)
- Blog page divined by categories.
The website should have places for display banners eg. a sidebar.
I will provide some screen shots of websites we like. You can always visit our existing website www.velorimo.gr to see it for yourself.

Target Market(s)

people seeking for future telling - astrologer services via phone. People who like to be informed about everyday astrology predictions

Industry/Entity Type

Astrology - tarot services via phone

Coding

Coded - Design and coding required

Number of Pages Required

5+ page

Font styles to use
Decorative
Script

Colors
6B429C
8869AF
B7A5CE
E3DAEB
F3F0F8

Requirements
Must have
• -Home page -Astrologers page -Phone packages page (eshop) -Blog page with categories - Made following the guidelines of quenbly so as to be efficient in quenbly ads marketing. Mobile friendly.
Nice to have
• Nice call to action buttons to call or buy packages. Sidebar with banner ads of maybe our offers.

```html
<!DOCTYPE html>
<html lang="el">
<head>
<meta charset="utf-8">
<title>velorimo.gr</title>
<link href="https://fonts.googleapis.com/css2?family=IBM+Plex+Sans:wght@400;500;600;700&family=Noto+Serif:wght@400&display=swap" rel="stylesheet">
<style>
:root{
  --purple:#6B429C;
  --purple-mid:#8869AF;
  --lilac:#B7A5CE;
  --lilac-light:#E3DAEB;
  --lilac-bg:#F3F0F8;
  --ink:#1b1b1b;
  --text:#333;
  --white:#fff;
}
*{box-sizing:border-box;margin:0;padding:0}
html,body{width:1200px;height:2823px;overflow:hidden}
body{position:relative;background:var(--white);font-family:"IBM Plex Sans",sans-serif;color:var(--ink)}
.abs{position:absolute}
a{color:inherit;text-decoration:none}

/* header */
.site-header{position:absolute;left:0;top:0;width:1200px;height:102px;background:var(--white)}
.brand{position:absolute;left:132px;top:22px;font-size:40px;font-weight:500;color:var(--ink);letter-spacing:-0.5px;display:flex;align-items:center;gap:8px}
.brand-dot{width:26px;height:26px;border-radius:50%;background:#9b8f95}
.search{position:absolute;left:570px;top:13px;width:187px;height:32px;border:1px solid #999;font-size:11px;color:#777;padding:8px 10px}
.search svg{position:absolute;right:9px;top:9px}
.call-top{position:absolute;left:778px;top:0;width:290px;height:48px;background:var(--purple);color:var(--white);display:flex;align-items:center;gap:10px;padding-left:16px;font-size:19px}
.call-top b{font-size:34px;font-weight:500}
.main-nav{position:absolute;top:66px;left:566px;display:flex;gap:34px;font-size:13px;font-weight:500}
.main-nav .active{color:var(--purple)}

/* hero */
.hero{position:absolute;left:0;top:102px;width:1200px;height:486px;background:radial-gradient(circle at 45% 35%,#4f8fd6 0%,#1d3a86 30%,#0d1848 65%,#090f30 100%)}
.hero-art{position:absolute;left:0;top:0;width:700px;height:486px;background:radial-gradient(circle at 430px 170px,rgba(180,210,255,.55) 0,rgba(80,130,220,.25) 120px,transparent 200px),linear-gradient(180deg,transparent 60%,rgba(196,140,110,.55) 90%,transparent)}
.hero-title{position:absolute;left:755px;top:82px;font-size:41px;font-weight:700;line-height:48px;color:var(--white)}
.btn{display:flex;align-items:center;justify-content:center;background:var(--purple);color:var(--white);font-weight:600;text-transform:uppercase}
.hero-btn{position:absolute;left:760px;top:310px;width:233px;height:51px;font-size:15px}
.dots{position:absolute;left:569px;top:441px;display:flex;gap:6px}
.dots i{width:11px;height:11px;border:1.5px solid #fff;border-radius:50%}
.dots i.on{background:rgba(255,255,255,.5)}

/* section headings */
.sec-title{position:absolute;font-size:19px;font-weight:700;text-transform:uppercase}
.sec-title::after{content:"";position:absolute;left:0;bottom:-12px;width:104px;height:2px;background:var(--purple)}
.sec-title.center{transform:translateX(-50%)}
.sec-title.center::after{left:50%;transform:translateX(-50%);width:54px}

/* blog cards */
.post{position:absolute;width:278px;height:409px;background:var(--white);box-shadow:0 2px 10px rgba(0,0,0,.08)}
.post .media{height:169px}
.post .meta{font-family:"Noto Serif",serif;font-size:10px;color:#444;margin:22px 28px 0}
.post h3{font-family:"Noto Serif",serif;font-weight:400;font-size:13.5px;line-height:22px;margin:8px 28px 0;text-transform:uppercase}
.post p{font-family:"Noto Serif",serif;font-size:10px;line-height:14.5px;margin:8px 28px 0;color:var(--text)}
.post .btn{position:absolute;left:28px;bottom:32px;width:169px;height:32px;font-size:11px}
.side-banner{position:absolute;left:755px;top:657px;width:309px;height:457px;background:linear-gradient(170deg,#6a56a8,#3a2a6e 45%,#5b38a0 70%,#2f1f66);color:#fff;text-align:center}
.side-banner .line1{position:absolute;top:168px;width:100%;font-size:33px;line-height:31px;font-weight:500}
.side-banner .band{position:absolute;left:0;bottom:0;width:100%;height:113px;background:rgba(40,25,90,.85);font-size:34px;line-height:36px;font-weight:700;color:#35c6f0;padding-top:20px}

/* astrologers */
.astro-band{position:absolute;left:0;top:1603px;width:1200px;height:577px;background:var(--lilac-bg)}
.astro{position:absolute;top:1708px;width:298px;height:369px;background:var(--white)}
.astro .media{height:172px}
.astro h3{font-family:"Noto Serif",serif;font-weight:400;font-size:15px;margin:20px 29px 0;text-transform:uppercase}
.astro p{font-family:"Noto Serif",serif;font-size:11px;line-height:16px;margin:12px 29px 0;color:var(--text)}
.astro .call{position:absolute;left:29px;bottom:0;width:136px;height:59px;background:var(--purple);color:#fff;display:flex;align-items:center;gap:8px;padding-left:14px}
.call small{display:block;font-size:11px;font-weight:600}
.call b{display:block;font-size:22px;line-height:22px}
.btn-outline{position:absolute;left:540px;top:2111px;width:120px;height:31px;border:2px solid var(--purple);color:var(--purple);font-size:11px;font-weight:600;display:flex;align-items:center;justify-content:center}

/* packages */
.pack{position:absolute;top:2296px;width:301px;height:224px;color:#fff;overflow:hidden}
.pack .big{position:absolute;font-size:30px;font-weight:700;line-height:28px;color:#2fb8ec}
.pack .small{position:absolute;font-size:15px;line-height:15px;color:#2fb8ec}
.pack .price{position:absolute;font-size:32px;font-weight:700}
.pack .price span{font-size:15px;font-weight:400;color:#dfe}
.pack-btn{position:absolute;left:520px;top:2555px;width:160px;height:37px;font-size:11px}

/* footer */
.site-footer{position:absolute;left:0;top:2647px;width:1200px;height:176px;background:var(--purple);color:#fff}
.site-footer .brand{color:#fff;top:36px}
.site-footer .brand-dot{background:#d8cfe6}
.foot-nav{position:absolute;top:46px;left:562px;display:flex;gap:34px;font-size:13px;font-weight:500}
.foot-rule{position:absolute;left:132px;top:93px;width:938px;height:1px;background:rgba(255,255,255,.25)}
.copy{position:absolute;top:131px;width:100%;text-align:center;font-size:11px}
</style>
</head>
<body>

<header class="site-header">
  <a class="brand" href="#">velorimo <span class="brand-dot"></span></a>
  <div class="search">Αναζήτηση
    <svg width="10" height="10" viewBox="0 0 10 10"><circle cx="4" cy="4" r="3" fill="none" stroke="#333" stroke-width="1.3"/><line x1="6.3" y1="6.3" x2="9" y2="9" stroke="#333" stroke-width="1.3"/></svg>
  </div>
  <a class="call-top" href="#">
    <svg width="22" height="22" viewBox="0 0 24 24"><path d="M6.6 10.8a15 15 0 0 0 6.6 6.6l2.2-2.2c.3-.3.7-.4 1-.2 1.1.4 2.3.6 3.6.6.6 0 1 .4 1 1V20c0 .6-.4 1-1 1A17 17 0 0 1 3 4c0-.6.4-1 1-1h3.5c.6 0 1 .4 1 1 0 1.3.2 2.5.6 3.6.1.3 0 .7-.2 1z" fill="#fff"/></svg>
    Καλέστε μας <b>14970</b>
  </a>
  <nav class="main-nav"><a class="active" href="#">ΣΠΊΤΙ</a><a href="#">ΙΣΤΟΛΌΓΙΟ</a><a href="#">ΜΈΝΤΙΟΥΜ ΑΣΤΡΟΛΌΓΟΙ</a><a href="#">ΑΓΟΡΆ ΧΡΌΝΟΥ ΟΜΙΛΊΑΣ</a></nav>
</header>

<section class="hero">
  <div class="hero-art" role="img" aria-label="Ανοιχτά χέρια κρατούν φωτεινό ζωδιακό κύκλο με τη σελήνη στο κέντρο, σε έναστρο ουρανό"></div>
  <h1 class="hero-title">ΤΑ ΖΏΔΙΑ ΓΙΑ<br>ΣΉΜΕΡΑ<br>ΠΑΡΑΣΚΕΥΉ<br>18/11</h1>
  <a class="btn hero-btn" href="#">ΔΙΑΒΆΣΤΕ ΠΕΡΙΣΣΌΤΕΡΑ</a>
  <div class="dots"><i></i><i class="on"></i><i></i><i></i></div>
</section>

<h2 class="sec-title" style="left:134px;top:626px">ΤΕΛΕΥΤΑΊΟ BLOG</h2>

<article class="post" style="left:135px;top:707px">
  <div class="media" role="img" aria-label="Χέρια απλώνουν κάρτες ταρώ ανάμεσα σε αναμμένα κεριά" style="background:linear-gradient(135deg,#b9aea4,#7d6d60 50%,#c9a36a)"></div>
  <div class="meta">17 Νοεμβρίου 2022 &nbsp;|&nbsp; by Velorimo</div>
  <h3>Τα ζώδια για σήμερα Παρασκευή 18/11</h3>
  <p>Έξτρα υποχρεώσεις εμφανίζονται που ζητούν διευθέτηση και όσο το δυνατόν πιο άμεσα. Απογοητεύεστε από την επαγγελματική σας πορεία, αλλά ευτυχώς προσωρινά.</p>
  <a class="btn" href="#">ΔΙΑΒΆΣΤΕ ΠΕΡΙΣΣΌΤΕΡΑ</a>
</article>

<article class="post" style="left:440px;top:707px">
  <div class="media" role="img" aria-label="Σύννεφο πάνω από μια σκάλα σε μπλε φόντο" style="background:linear-gradient(160deg,#3346a6,#2a3c98 60%,#4a5dc0)"></div>
  <div class="meta">17 Νοεμβρίου 2022 &nbsp;|&nbsp; by Velorimo</div>
  <h3>Τα ζώδια για σήμερα Πέμπτη 17/11</h3>
  <p>Θα αισθανθείτε έντονη την ανάγκη να αποτραβηχτείτε από το κοινωνικό γίγνεσθαι, και να μείνετε στον προσωπικό σας χώρο, ερχόμενοι έτσι, σε επαφή με τον εαυτό σας για μια καλή συζήτηση μαζί του.</p>
  <a class="btn" href="#">ΔΙΑΒΆΣΤΕ ΠΕΡΙΣΣΌΤΕΡΑ</a>
</article>

<aside class="side-banner" role="img" aria-label="Διαφημιστικό: κάρτες με μυστικιστική διακόσμηση σε μωβ φόντο">
  <div class="line1">Μίλησε Χωρίς<br>χρεώσεις στο<br>τηλέφωνό σου..!</div>
  <div class="band">Μάθε πως<br>γίνεται..!!!</div>
</aside>

<article class="post" style="left:135px;top:1141px">
  <div class="media" role="img" aria-label="Ζωγραφιά με δύο φλιτζάνια σε έντονα χρώματα" style="background:linear-gradient(120deg,#e2d4a8,#5aa4c8 35%,#c94b3a 70%,#e8c070)"></div>
  <div class="meta">17 Νοεμβρίου 2022 &nbsp;|&nbsp; by Velorimo</div>
  <h3>Ταρώ για σήμερα Τετάρτη 16/11</h3>
  <p>Καλή υγεία και επιτυχίες σας περιμένουν σήμερα. Υπερισχύει η αρετή και το θάρρος, έναντι των παθών, η τόλμη έναντι των αμφιβολιών. Καθώς αποκτάτε τον έλεγχο των επιθυμιών σας, όλα είναι εφικτά.</p>
  <a class="btn" href="#">ΔΙΑΒΆΣΤΕ ΠΕΡΙΣΣΌΤΕΡΑ</a>
</article>

<article class="post" style="left:440px;top:1141px">
  <div class="media" role="img" aria-label="Αναμμένο κερί στο σκοτάδι" style="background:radial-gradient(circle at 45% 55%,#c05a20 0,#4a2010 18%,#140b06 45%,#0a0604)"></div>
  <div class="meta">17 Νοεμβρίου 2022 &nbsp;|&nbsp; by Velorimo</div>
  <h3>Τα ζώδια για σήμερα Τετάρτη 16/11</h3>
  <p>Θα αισθανθείτε έντονη την ανάγκη να αποτραβηχτείτε στον προσωπικό σας χώρο και δη στο σπίτι σας, όπου η επαφή με τα πρόσωπα της οικογένειάς σας, σας γαληνεύει από το άγχος.</p>
  <a class="btn" href="#">ΔΙΑΒΆΣΤΕ ΠΕΡΙΣΣΌΤΕΡΑ</a>
</article>

<article class="post" style="left:762px;top:1141px">
  <div class="media" role="img" aria-label="Εικονογράφηση με ταχυδακτυλουργό και καπέλο" style="background:linear-gradient(135deg,#f2f0d8,#c8d8e8 50%,#7a8fb0)"></div>
  <div class="meta">17 Νοεμβρίου 2022 &nbsp;|&nbsp; by Velorimo</div>
  <h3>Ταρώ για σήμερα Τρίτη 15/11</h3>
  <p>Αν ακολουθήσετε κατά γράμμα τις προσταγές του συμπαντικού νόμου, και βάλετε πειθαρχία στη ζωή και την καθημερινότητά σας, θα απολαύσετε την επίτευξη όλων των στόχων σας.</p>
  <a class="btn" href="#">ΔΙΑΒΆΣΤΕ ΠΕΡΙΣΣΌΤΕΡΑ</a>
</article>

<section class="astro-band"></section>
<h2 class="sec-title center" style="left:600px;top:1635px">ΑΣΤΡΟΛΌΓΟΙ</h2>

<article class="astro" style="left:132px">
  <div class="media" role="img" aria-label="Πορτρέτο αστρολόγου σε ζεστό φόντο με τον αριθμό κλήσης" style="background:linear-gradient(120deg,#8a3a2a,#2a1a14 50%,#c08a20)"></div>
  <h3>Ελένη Καραλή</h3>
  <p>Αστρολόγος με εξειδίκευση στην Αστροψυχολογία, με πολλά χρόνια έρευνας πάνω στις ανθρώπινες σχέσεις. Κάλεσε τώρα για μια προσωπική αστρολογική πρόβλεψη.</p>
  <a class="call" href="#"><svg width="22" height="22" viewBox="0 0 24 24"><path d="M6.6 10.8a15 15 0 0 0 6.6 6.6l2.2-2.2c.3-.3.7-.4 1-.2 1.1.4 2.3.6 3.6.6.6 0 1 .4 1 1V20c0 .6-.4 1-1 1A17 17 0 0 1 3 4c0-.6.4-1 1-1h3.5c.6 0 1 .4 1 1 0 1.3.2 2.5.6 3.6.1.3 0 .7-.2 1z" fill="#fff"/></svg><span><small>Καλέστε μας</small><b>14970</b></span></a>
</article>

<article class="astro" style="left:451px">
  <div class="media" role="img" aria-label="Πορτρέτο αστρολόγου σε νυχτερινό φόντο με φεγγάρι και τον αριθμό κλήσης" style="background:linear-gradient(120deg,#1a2a6a,#0e1440 50%,#c0186a)"></div>
  <h3>Δανάη Μορφή</h3>
  <p>Πανίσχυρο μέντιουμ. Θα σας βοηθήσω να επιλύσετε τα ερωτικά και επαγγελματικά σας προβλήματα με σίγουρες απαντήσεις μέσω της επιστήμης της αστρολογίας.</p>
  <a class="call" href="#"><svg width="22" height="22" viewBox="0 0 24 24"><path d="M6.6 10.8a15 15 0 0 0 6.6 6.6l2.2-2.2c.3-.3.7-.4 1-.2 1.1.4 2.3.6 3.6.6.6 0 1 .4 1 1V20c0 .6-.4 1-1 1A17 17 0 0 1 3 4c0-.6.4-1 1-1h3.5c.6 0 1 .4 1 1 0 1.3.2 2.5.6 3.6.1.3 0 .7-.2 1z" fill="#fff"/></svg><span><small>Καλέστε μας</small><b>14970</b></span></a>
</article>

<article class="astro" style="left:771px">
  <div class="media" role="img" aria-label="Πορτρέτο αστρολόγου σε πράσινο φόντο με αριθμούς και τον αριθμό κλήσης" style="background:linear-gradient(120deg,#0e5a5a,#7aa8a8 50%,#d8c020)"></div>
  <h3>Ιφιγένεια Λάμπρου</h3>
  <p>Η τριαντάχρονη έρευνα στην αστρολογία μου έμαθε ότι μπορούμε να αποφύγουμε τις κακοτοπιές και να βοηθήσουμε στην ευημερία μας.</p>
  <a class="call" href="#"><svg width="22" height="22" viewBox="0 0 24 24"><path d="M6.6 10.8a15 15 0 0 0 6.6 6.6l2.2-2.2c.3-.3.7-.4 1-.2 1.1.4 2.3.6 3.6.6.6 0 1 .4 1 1V20c0 .6-.4 1-1 1A17 17 0 0 1 3 4c0-.6.4-1 1-1h3.5c.6 0 1 .4 1 1 0 1.3.2 2.5.6 3.6.1.3 0 .7-.2 1z" fill="#fff"/></svg><span><small>Καλέστε μας</small><b>14970</b></span></a>
</article>

<a class="btn-outline" href="#">ΠΡΟΒΟΛΉ ΌΛΩΝ</a>

<h2 class="sec-title center" style="left:600px;top:2224px">ΠΑΚΈΤΑ</h2>

<a class="pack" href="#" style="left:132px;background:radial-gradient(circle at 30% 50%,#1c4ea8,#0a1a4a 60%,#060c26)" role="img" aria-label="Πακέτο 30 λεπτών χρόνου ομιλίας, εικόνα χρονομέτρου">
  <span class="big" style="left:180px;top:18px;text-align:right">30’<br>ΛΕΠΤΑ</span>
  <span class="small" style="left:196px;top:78px">ΧΡΟΝΟΥ<br>ΟΜΙΛΙΑΣ</span>
  <span class="price" style="left:198px;top:154px;line-height:30px"><span>ΜΟΝΟ</span><br>30€</span>
</a>
<a class="pack" href="#" style="left:452px;background:linear-gradient(135deg,#0a1e4a,#0c3a6a 50%,#0a1e4a)" role="img" aria-label="Πακέτο 60 λεπτών χρόνου ομιλίας, εικόνα ηχητικού κύματος">
  <span class="big" style="left:26px;top:12px">60’ ΛΕΠΤΑ</span>
  <span class="small" style="left:215px;top:12px;font-size:12px;line-height:12px">ΧΡΟΝΟΥ<br>ΟΜΙΛΙΑΣ</span>
  <span class="price" style="left:139px;top:176px"><span>ΜΟΝΟ</span> 50€</span>
</a>
<a class="pack" href="#" style="left:769px;background:linear-gradient(150deg,#0c2a3a,#051018 55%,#0a2030)" role="img" aria-label="Πακέτο 120 λεπτών χρόνου ομιλίας, εικόνα με σκιαγραφία και σκορπισμένα γράμματα">
  <span class="big" style="left:10px;top:150px">120’ ΛΕΠΤΑ</span>
  <span class="small" style="left:12px;top:180px;font-size:18px">ΧΡΟΝΟΥ ΟΜΙΛΙΑΣ</span>
  <span class="price" style="left:215px;top:152px;line-height:30px"><span style="font-size:20px">ΜΟΝΟ</span><br>75€</span>
</a>

<a class="btn pack-btn" href="#">ΔΕΊΤΕ ΌΛΑ ΤΑ ΠΑΚΈΤΑ</a>

<footer class="site-footer">
  <a class="brand" href="#">velorimo <span class="brand-dot"></span></a>
  <nav class="foot-nav"><a href="#">ΣΠΊΤΙ</a><a href="#">ΙΣΤΟΛΌΓΙΟ</a><a href="#">ΜΈΝΤΙΟΥΜ ΑΣΤΡΟΛΌΓΟΙ</a><a href="#">ΑΓΟΡΆ ΧΡΌΝΟΥ ΟΜΙΛΊΑΣ</a></nav>
  <div class="foot-rule"></div>
  <div class="copy">Copyright © 2022 All Rights Reserved</div>
</footer>

</body>
</html>
```